Business Card Design for Vintage Jazz

I am a vintage jazz band leader in New York City. My groups play the music of the 1920s, 1930s and 1940s. My website is morvalquist.com for more info on what I do.

I am looking for a two sided business card design that has the look and feel of a really nice business card from the 1930s. I need to convey with the design that my work has that vintage kind of class and style, but also conveys that we are fun and entertaining.

Most importantly it should make a bold staement. If Hal Denbrook had a card, what would it have looked like? I want a card that I feel confident will make an impact and will let people know that my work is te the top that NYC has to offer in vintage jazz..

Note that I have only decided to avoid the "committed payment" option as I have not used this service before. Assuming that I get quality work I will select a design from those presented.

Target Market(s)

people who want to hire my band for events, media, and new fans of the band

Industry/Entity Type

Performing Art

Contact Information for Business Card

Definitely a matte finish, possibly a sort of old style of paper with that brown tint? definitely a thick card.

Requirements
Must have
• FRONT
• My name: Tobin Vashley
• What I do: Bandleader, Guitarist, Vocalist, Songwriter
• Contact Details: morvalquist.com tobin@morvalquist.com 646-555-0148
• BACK
• My Social Media Links:
• fanpage.morvalquist.com
• twitter, instagram, linkedin: morvalquist
• I'm also including a photo image I would like to use. The photo's background is not needed, and to be honest isn't really desireable. Just looking to use the image of me.
Nice to have
• I'm attaching which could be used as is, omitted from the card, or altered maybe with text going around the outside of the circle or in some other way. It may need some clean up to the edges of the lettering as we only use it for the website thumbnail.
• If there's space I'd like to include the text "join our mailing list for a free song download: freesong.morvalquist.com" If not perhaps just "Download a Free Song at: freesong.morvalquist.com - something to this end.
Should not have
• anything cartoony. Don't think retro 90s's vision of the swing era, think actual swing era!
• anything modern. Got to look old school
• Try to avoid dark backgrounds. Since we often play in bars and clubs where it is dar, a d
• avoid script fonts.

```html
<!DOCTYPE html>
<html lang="en">
<head>
<meta charset="utf-8">
<title>Tobin Vashley – Business Card</title>
<link rel="stylesheet" href="https://fonts.googleapis.com/css2?family=Open+Sans:wght@400;600;700&display=swap">
<style>
  :root {
    --ink: #0b0b0b;
    --paper: #ffffff;
    --backdrop: #d9d9d9;
    --teal: #5fc4ad;
    --teal-deep: #3f9e8a;
  }
  * { box-sizing: border-box; margin: 0; padding: 0; }
  html, body { width: 1200px; height: 900px; overflow: hidden; }
  body {
    background: var(--backdrop);
    font-family: "Open Sans", Arial, sans-serif;
    position: relative;
  }
  .card {
    position: absolute;
    width: 640px;
    height: 366px;
    border-radius: 26px;
    overflow: hidden;
    background: var(--paper);
    box-shadow: 0 10px 28px rgba(0,0,0,0.25);
  }

  /* ---------- Card back: monogram side ---------- */
  .card--back { left: 80px; top: 50px; }
  .brand-disc {
    position: absolute;
    left: 96px; top: 86px;
    width: 206px; height: 206px;
    border-radius: 50%;
    background: var(--ink);
    display: flex; align-items: center; justify-content: center;
  }
  .brand-disc__name {
    color: var(--paper);
    font-weight: 600;
    font-size: 18px;
    letter-spacing: 1.5px;
    text-transform: uppercase;
  }
  .download-pill {
    position: absolute;
    right: 0; top: 104px;
    width: 316px; height: 68px;
    background: var(--ink);
    border-radius: 34px 0 0 34px;
    color: var(--paper);
    padding: 13px 0 0 28px;
  }
  .download-pill__lead {
    font-weight: 600;
    font-size: 15px;
    letter-spacing: 0.8px;
    text-transform: uppercase;
  }
  .download-pill__url { font-size: 13px; margin-top: 2px; letter-spacing: 0.3px; }
  .social {
    position: absolute;
    left: 46px; top: 302px;
    color: var(--ink);
    font-size: 15px;
    letter-spacing: 0.3px;
  }
  .social__row { display: flex; align-items: center; gap: 8px; height: 25px; }
  .social__dot {
    width: 10px; height: 10px;
    border-radius: 50%;
    background: var(--ink);
    flex: none;
  }

  /* ---------- Card front: contact side ---------- */
  .card--front { left: 480px; top: 470px; }
  .front-rule {
    position: absolute;
    left: 0; right: 0;
    top: 136px; height: 3px;
    background: var(--ink);
  }
  .front-band {
    position: absolute;
    left: 0; right: 0;
    top: 148px; bottom: 0;
    background: var(--ink);
  }
  .portrait {
    position: absolute;
    left: 318px; top: 24px;
    width: 166px; height: 166px;
    border-radius: 50%;
    border: 5px solid var(--paper);
    background: radial-gradient(circle at 50% 45%, var(--teal) 55%, var(--teal-deep) 100%);
  }
  .identity {
    position: absolute;
    right: 332px; top: 230px;
    text-align: right;
    color: var(--paper);
  }
  .identity__name {
    font-weight: 700;
    font-size: 25px;
    letter-spacing: 1px;
    text-transform: uppercase;
    line-height: 1.1;
  }
  .identity__role {
    font-size: 14.5px;
    letter-spacing: 0.8px;
    text-transform: uppercase;
    line-height: 1.3;
  }
  .divider {
    position: absolute;
    left: 318px; top: 228px;
    width: 1.5px; height: 84px;
    background: var(--paper);
  }
  .contact {
    position: absolute;
    left: 334px; top: 236px;
    color: var(--paper);
    font-size: 14px;
    line-height: 1.5;
    letter-spacing: 0.3px;
  }
  .contact__label { font-weight: 700; }
</style>
</head>
<body>

  <section class="card card--back" aria-label="Card back">
    <div class="brand-disc"><span class="brand-disc__name">Tobin Vashley</span></div>
    <div class="download-pill">
      <p class="download-pill__lead">Download a free song at</p>
      <p class="download-pill__url">www.freesong.morvalquist.com</p>
    </div>
    <div class="social">
      <div class="social__row"><span class="social__dot"></span>fanpage.morvalquist.com</div>
      <div class="social__row"><span class="social__dot"></span>morvalquist</div>
    </div>
  </section>

  <section class="card card--front" aria-label="Card front">
    <div class="front-rule"></div>
    <div class="front-band"></div>
    <div class="portrait" role="img" aria-label="Photo of the bandleader in a dark suit tipping a straw boater hat"></div>
    <div class="identity">
      <p class="identity__name">Tobin Vashley</p>
      <p class="identity__role">Bandleader, Guitarist</p>
      <p class="identity__role">Vocalist, Songwriter</p>
    </div>
    <div class="divider"></div>
    <div class="contact">
      <p><span class="contact__label">P:</span> 646-555-0148</p>
      <p><span class="contact__label">E:</span> tobin@morvalquist.com</p>
      <p><span class="contact__label">W:</span> www.morvalquist.com</p>
    </div>
  </section>

</body>
</html>
```